Provide bookkeeping and accounting services to small and growing businesses

We need website and logo design using the name Dornaby as the logo.
The target audience are small companies and startups who need:
1) Simple bookkeeping services
2) Accounting advice that only someone with many years of senior financial experience as a CPA can provide.

The services are provided by two individuals. each of whom specialize in one of the areas.

We want the website to be clean without a lot of visual distraction but don't know how to make a boring subject interesting. We believe our potential clients, small business owners, need to find what they want quickly and easily without a lot of verbiage or distractions.

We've attached a draft of the homepage and have completed the text on most of the other pages.

Target Market(s)

small and early stage growth companies in San Diego North County

Industry/Entity Type

Accounting

Number of Pages Required

1 page

Font styles to use
Sans Serif

Colors
86cfc6
33b8a4
85cae6

Requirements
Must have
• We need a design for the website homepage that includes the name Dornaby as the logo. Must include a design for the name.
• Must have color in teal or greenish blue.
Nice to have
• White background, clean, clear, uncluttered.
• We would like to use the design in a Theme on a WordPress website. Themes Paper Lantern and Quiet Harbour are appealing to us.
Should not have
• Moving pictures

```html
<!DOCTYPE html>
<html lang="en">
<head>
<meta charset="utf-8">
<title>Dornaby Accounting and Bookkeeping</title>
<link href="https://fonts.googleapis.com/css2?family=Ubuntu:wght@400;500&family=Lato:wght@400;700&family=Source+Serif+4:wght@500&display=swap" rel="stylesheet">
<style>
:root{
  --teal:#33b8a4;
  --teal-soft:#86cfc6;
  --teal-active:#6cc1b6;
  --sky:#85cae6;
  --ink:#222;
  --body:#444;
  --muted:#8a8a8a;
  --rule:#d6d6d6;
  --footer:#1d1d1d;
  --footer-text:#e8e8e8;
}
*{box-sizing:border-box;margin:0;padding:0}
html,body{width:1200px;height:2344px;overflow:hidden;background:#fff}
body{position:relative;font-family:"Lato",sans-serif;color:var(--body)}
section,header,nav,footer{position:absolute;left:0;width:1200px}
.abs{position:absolute}

/* header */
.site-header{top:0;height:103px}
.brand-name{left:102px;top:4px;font:400 50px/1 "Ubuntu",sans-serif;color:var(--teal)}
.brand-tag{left:101px;top:64px;font:400 17px/1 "Ubuntu",sans-serif;color:#333}
.contact-chip{top:26px;display:flex;gap:10px;align-items:flex-start;font:400 14.5px/1.35 "Ubuntu",sans-serif;color:#222}
.contact-chip svg{flex:none}
.chip-phone{left:750px}
.chip-mail{left:912px}

/* nav */
.main-nav{top:103px;height:42px;background:var(--teal-soft)}
.main-nav ul{list-style:none;position:absolute;left:98px;top:0;display:flex;height:42px}
.main-nav li{height:42px;line-height:42px;text-align:center;color:#fff;font:400 16px/42px "Ubuntu",sans-serif;border-right:1px solid rgba(255,255,255,.35)}
.main-nav li.is-active{background:var(--teal-active)}

/* hero */
.hero{top:145px;height:541px;background:linear-gradient(100deg,#1b1b1b 0%,#4a4540 30%,#7b7168 55%,#b8b0a6 75%,#e6e3de 100%)}
.hero-title{left:100px;top:190px;font:500 37px/50px "Source Serif 4",serif;color:#fff;text-shadow:0 2px 4px rgba(0,0,0,.45)}
.hero-dots{left:576px;top:506px;display:flex;gap:7px}
.hero-dots span{width:11px;height:11px;border-radius:50%;background:var(--teal)}
.hero-dots span.on{background:#fff;border:2px solid var(--teal)}

/* shared */
.section-title{width:1200px;text-align:center;font:400 33px/1 "Ubuntu",sans-serif;color:var(--ink)}
.section-title em{font-style:normal;color:var(--teal)}
.title-rule{left:422px;width:359px;height:2px;background:var(--rule)}
.title-rule::after{content:"";position:absolute;left:174px;top:-3px;width:8px;height:8px;border-radius:50%;background:#c8c8c8}
.btn{display:flex;align-items:center;justify-content:center;gap:8px;color:#fff;font:700 12.5px/1 "Lato",sans-serif;text-transform:uppercase}
.btn-arrow{width:20px;height:20px;border-radius:50%;background:#fff;display:flex;align-items:center;justify-content:center}

/* welcome */
.welcome{top:686px;height:322px}
.welcome .section-title{top:46px}
.welcome .title-rule{top:94px}
.welcome-copy{left:102px;top:118px;width:992px;text-align:center;font:400 12.5px/25px "Lato",sans-serif;color:#333}
.welcome .btn{left:539px;top:237px;width:117px;height:35px;background:var(--sky)}
.welcome .btn-arrow{color:var(--sky)}

/* services */
.services{top:1008px;height:406px;background:var(--teal);color:#fff}
.services-title{left:102px;top:36px;font:400 34px/1 "Ubuntu",sans-serif}
.services-line{left:309px;top:58px;width:425px;height:1px;background:rgba(255,255,255,.7)}
.service-icon{width:128px;height:128px;border-radius:50%;background:rgba(255,255,255,.3);display:flex;align-items:center;justify-content:center}
.service-name{font:700 19px/1 "Lato",sans-serif}
.service-text{width:290px;font:400 14px/22px "Lato",sans-serif}
.service-btn{width:94px;height:34px;border:2px solid rgba(255,255,255,.8);background:rgba(255,255,255,.2);font:400 13.5px/30px "Lato",sans-serif;text-align:center}
.connector{left:290px;top:100px}

.inquiry-card{left:795px;top:39px;width:305px;height:331px;background:#fff;box-shadow:0 3px 8px rgba(0,0,0,.25)}
.inquiry-head{left:809px;top:31px;width:277px;height:42px;background:var(--sky);text-align:center;font:400 25px/42px "Ubuntu",sans-serif}
.field{left:24px;width:264px;height:34px;border:1px solid #e2e2e2;background:linear-gradient(#fff,#f4f4f4);display:flex;align-items:center;font:400 13px/1 "Lato",sans-serif;color:#555}
.field-icon{width:38px;height:100%;border-right:1px solid #e2e2e2;display:flex;align-items:center;justify-content:center;flex:none}
.field span{padding-left:10px}
.field-message{height:84px;align-items:flex-start}
.field-message span{padding-top:12px}
.inquiry-card .btn{left:25px;top:281px;width:118px;height:35px;background:var(--sky);font-size:12px}
.inquiry-card .btn-arrow{color:var(--sky)}

/* reviews */
.reviews{top:1414px;height:353px}
.reviews .section-title{top:50px}
.reviews .title-rule{top:96px}
.avatar{width:86px;height:86px;border-radius:50%;background:linear-gradient(#d9c2ad,#9f8571);border:4px solid #fff;box-shadow:0 0 0 2px #cfcfcf}
.review-text{width:362px;font:400 15px/23.4px "Lato",sans-serif;color:#333}
.review-text .q{color:#c5d2dc;font:700 30px/0 "Lato",sans-serif;vertical-align:-10px}
.review-name{font:700 16px/1 "Lato",sans-serif;color:var(--teal)}
.review-divider{left:598px;top:141px;width:1px;height:125px;background:#e6e6e6}
.review-arrow{top:178px}

/* call to action */
.cta{top:1767px;height:281px;background:linear-gradient(90deg,#8ccbe6 0%,#95cee6 40%,#7fbede 75%,#6aaed1 100%)}
.cta-text{left:0;top:38px;width:1200px;text-align:center;font:400 31px/45px "Ubuntu",sans-serif;color:#fff}
.cta .btn{left:531px;top:199px;width:138px;height:37px;background:var(--teal);text-transform:none;font:400 16px/1 "Lato",sans-serif}
.cta .btn-arrow{color:var(--teal)}

/* footer */
.site-footer{top:2048px;height:252px;background:var(--footer);color:var(--footer-text)}
.footer-heading{top:29px;font:400 16px/1 "Ubuntu",sans-serif;padding-bottom:12px;border-bottom:1px dotted #555}
.footer-sep{top:28px;width:1px;height:196px;background:#333}
.quick-links{left:102px;top:70px;list-style:none;font:400 12.5px/23.8px "Lato",sans-serif}
.quick-links li::before{content:"›";margin-right:10px;color:#aaa}
.contact-row{left:294px;display:flex;gap:12px;font:700 12px/18px "Lato",sans-serif}
.contact-row.plain{font-weight:400}
.map-area{left:583px;top:74px;width:255px;height:136px;background:linear-gradient(#e9ecef,#dfe4e8);border:2px solid #fff}
.footer-brand{left:875px;top:88px;width:325px;text-align:center}
.footer-brand .name{font:400 38px/1 "Ubuntu",sans-serif;color:#bdbdbd}
.footer-brand .tag{margin-top:6px;font:400 12.5px/1 "Ubuntu",sans-serif;color:#9a9a9a}
.social{left:944px;top:170px;display:flex;gap:10px}
.social span{width:24px;height:24px;border-radius:50%;border:2px solid #fff}
.social .s1{background:#3b5b9a}.social .s2{background:#1b78b4}.social .s3{background:#3ba6e0}.social .s4{background:#d9472f}

.copyright{position:absolute;left:0;top:2300px;width:1200px;height:44px;background:var(--teal);color:#fff;text-align:center;font:400 13px/44px "Lato",sans-serif}
</style>
</head>
<body>

<header class="site-header">
  <div class="abs brand-name">Dornaby</div>
  <div class="abs brand-tag">Accounting and Bookkeeping</div>
  <div class="abs contact-chip chip-phone">
    <svg width="34" height="42" viewBox="0 0 34 42"><path d="M10 3 C2 8 1 24 12 36 C15 39 19 41 22 40 L25 33 L18 28 L15 31 C10 26 9 18 11 13 L15 13 L16 5 Z" fill="none" stroke="var(--teal)" stroke-width="2.5" stroke-linejoin="round"/><path d="M20 12 A8 8 0 0 1 27 20 M20 6 A14 14 0 0 1 33 20" fill="none" stroke="var(--teal)" stroke-width="2"/></svg>
    <div>Call Us:<br>(012) 555 0147</div>
  </div>
  <div class="abs contact-chip chip-mail">
    <svg width="38" height="40" viewBox="0 0 38 40"><path d="M3 16 L22 3 L35 22 L16 35 Z" fill="none" stroke="var(--teal)" stroke-width="2.5" stroke-linejoin="round"/><path d="M3 16 L22 19 L22 3 M16 35 L22 19 L35 22" fill="none" stroke="var(--teal)" stroke-width="2"/></svg>
    <div>Mail Us:<br>info@dornaby.com</div>
  </div>
</header>

<nav class="main-nav">
  <ul>
    <li class="is-active" style="width:152px">Home</li>
    <li style="width:172px">About Us</li>
    <li style="width:169px">Services</li>
    <li style="width:170px">Experience</li>
    <li style="width:148px">Resources</li>
    <li style="width:188px">Contact Us</li>
  </ul>
</nav>

<section class="hero" role="img" aria-label="Photo of hands at a desk with a calculator, coffee cup and a printed bar chart">
  <h1 class="abs hero-title">Providing a full range of accounting,<br>tax, bookkeeping and business<br>consulting services</h1>
  <div class="abs hero-dots"><span></span><span class="on"></span><span></span></div>
</section>

<section class="welcome">
  <h2 class="abs section-title">Welcome To <em>Dornaby</em> Accounting and Bookkeeping</h2>
  <div class="abs title-rule"></div>
  <p class="abs welcome-copy">Lorem ipsum dolouar sit amet consec tetuer adipiscing elnit. Praebulum molesbeutie lacus. Aenea nonuendrerit maurihasellu porta. Fusce suscpvarius mi. Cum sociis natoque penatibus et magnis dis parturientontes nascetur ridiculus mus. Nulla dui. Fusce feugiat mal esuada odio. Morbi nunc odio gravida atcursus necuctus a lorem. Maecenas tristique orci ac sem uis ultricies pharetra magna. Donec accumsan malesuada orci.onec sit amet eros. Lorem ipsu m dolor sit amet consectetuer adipiscing elit. Mauris fermentum dictum reet aliquam leo tellus dolor dapibus eget elementum vel cursus eleifend elit.</p>
  <a class="abs btn">Read More <span class="btn-arrow"><svg width="10" height="10" viewBox="0 0 10 10"><path d="M3 1 L7 5 L3 9" fill="none" stroke="currentColor" stroke-width="2.2"/></svg></span></a>
</section>

<section class="services">
  <h2 class="abs services-title">Our Services</h2>
  <div class="abs services-line"></div>

  <div class="abs service-icon" style="left:116px;top:105px">
    <svg width="70" height="72" viewBox="0 0 70 72" fill="none" stroke="#fff" stroke-width="3"><rect x="24" y="18" width="34" height="48" rx="3"/><rect x="30" y="24" width="22" height="9"/><g fill="#fff" stroke="none"><rect x="30" y="38" width="5" height="5"/><rect x="38" y="38" width="5" height="5"/><rect x="46" y="38" width="5" height="5"/><rect x="30" y="46" width="5" height="5"/><rect x="38" y="46" width="5" height="5"/><rect x="46" y="46" width="5" height="5"/><rect x="30" y="54" width="5" height="5"/><rect x="38" y="54" width="5" height="5"/><rect x="46" y="54" width="5" height="5"/></g><path d="M20 8 C8 6 6 18 14 20 C22 22 22 34 10 32 M14 2 V38"/></svg>
  </div>
  <div class="abs service-icon" style="left:480px;top:105px">
    <svg width="64" height="72" viewBox="0 0 64 72" fill="none" stroke="#fff" stroke-width="3"><path d="M14 6 H44 L56 18 V66 H14 Z"/><path d="M8 12 V70 H48"/><path d="M44 6 V18 H56"/><path d="M30 26 C22 25 21 35 29 36 C37 37 37 47 27 46 M29 22 V50"/><path d="M38 32 H50 M38 40 H50 M22 56 H50"/></svg>
  </div>

  <svg class="abs connector" width="160" height="120" viewBox="0 0 160 120"><path d="M83 0 V64 M4 108 H156" stroke="#fff" stroke-width="1.5"/><path d="M0 108 L10 102 V114 Z M160 108 L150 102 V114 Z" fill="#fff"/></svg>

  <h3 class="abs service-name" style="left:98px;top:250px">Simple bookkeeping</h3>
  <p class="abs service-text" style="left:98px;top:276px">Lorem ipsum dolouar sit amet consec tetuerrt scing elnit. Praebulum molesbeutie lacus.</p>
  <a class="abs service-btn" style="left:98px;top:333px">Read More</a>

  <h3 class="abs service-name" style="left:472px;top:250px">Accounting advice</h3>
  <p class="abs service-text" style="left:472px;top:276px">Lorem ipsum dolouar sit amet consec tetuerrt scing elnit. Praebulum molesbeutie lacus.</p>
  <a class="abs service-btn" style="left:472px;top:333px">Read More</a>

  <form class="abs inquiry-card">
    <div class="abs field" style="top:47px"><span class="field-icon"><svg width="14" height="14" viewBox="0 0 14 14" fill="#999"><circle cx="7" cy="4" r="3.5"/><path d="M0 14 C0 8 14 8 14 14 Z"/></svg></span><span>Name</span></div>
    <div class="abs field" style="top:90px"><span class="field-icon"><svg width="13" height="13" viewBox="0 0 13 13" fill="#999"><path d="M2 0 L5 3 L3.5 5 C4.5 7.5 5.5 8.5 8 9.5 L10 8 L13 11 L11 13 C5 13 0 8 0 2 Z"/></svg></span><span>Phone</span></div>
    <div class="abs field" style="top:133px"><span class="field-icon"><svg width="14" height="10" viewBox="0 0 14 10" fill="#999"><path d="M0 0 H14 L7 5 Z M0 2 L7 7 L14 2 V10 H0 Z"/></svg></span><span>Email</span></div>
    <div class="abs field field-message" style="top:178px"><span class="field-icon"><svg width="14" height="14" viewBox="0 0 14 14" fill="none" stroke="#999" stroke-width="1.6"><path d="M9 2 H1 V13 H12 V6"/><path d="M5 9 L13 1" /></svg></span><span>Message</span></div>
    <a class="abs btn">Read More <span class="btn-arrow"><svg width="10" height="10" viewBox="0 0 10 10"><path d="M3 1 L7 5 L3 9" fill="none" stroke="currentColor" stroke-width="2.2"/></svg></span></a>
  </form>
  <div class="abs inquiry-head">Quick Inquiry</div>
</section>

<section class="reviews">
  <h2 class="abs section-title">Customer <em>Reviews</em></h2>
  <div class="abs title-rule"></div>

  <svg class="abs review-arrow" style="left:54px" width="20" height="40" viewBox="0 0 20 40"><path d="M18 2 L3 20 L18 38" fill="none" stroke="#bbb" stroke-width="2"/></svg>
  <svg class="abs review-arrow" style="left:1124px" width="20" height="40" viewBox="0 0 20 40"><path d="M2 2 L17 20 L2 38" fill="none" stroke="#bbb" stroke-width="2"/></svg>

  <div class="abs avatar" role="img" aria-label="Portrait of the client Marlo" style="left:99px;top:157px"></div>
  <p class="abs review-text" style="left:203px;top:136px"><span class="q">&ldquo;</span>&nbsp; Lorem ipsum dolor sit amet, onsectietuer icingr eliterei sed diam nonummy nibh euismod tincideuntr ut laoreet dolore gna roererrerweire aliquam eraterer lutpatei. Uti wisi enim ad miwinim veniam, quiserere istrud wer rreri tation. &nbsp;<span class="q">&rdquo;</span></p>
  <div class="abs review-name" style="left:203px;top:267px">- Marlo</div>

  <div class="abs review-divider"></div>

  <div class="abs avatar" role="img" aria-label="Portrait of the client Tessaly" style="left:629px;top:157px"></div>
  <p class="abs review-text" style="left:733px;top:136px"><span class="q">&ldquo;</span>&nbsp; Lorem ipsum dolor sit amet, onsectietuer icingr eliterei sed diam nonummy nibh euismod tincideuntr ut laoreet dolore gna roererrerweire aliquam eraterer lutpatei. Uti wisi enim ad miwinim veniam, quiserere istrud wer rreri tation. &nbsp;<span class="q">&rdquo;</span></p>
  <div class="abs review-name" style="left:733px;top:267px">- Tessaly</div>
</section>

<section class="cta" role="img" aria-label="Soft blue photo of business people standing in front of a hazy skyline">
  <p class="abs cta-text">Dornaby offers a flexible range of accounting and bookkeeping<br>services and support &nbsp;for small and growing organizations in San<br>Diego North County.</p>
  <a class="abs btn">Call Us Today <span class="btn-arrow"><svg width="10" height="10" viewBox="0 0 10 10"><path d="M3 1 L7 5 L3 9" fill="none" stroke="currentColor" stroke-width="2.2"/></svg></span></a>
</section>

<footer class="site-footer">
  <h4 class="abs footer-heading" style="left:102px;width:110px">Quick Links</h4>
  <ul class="abs quick-links">
    <li>Home</li><li>About Us</li><li>Services</li><li>Experience</li><li>Resources</li><li>Contact Us</li>
  </ul>
  <div class="abs footer-sep" style="left:250px"></div>

  <h4 class="abs footer-heading" style="left:294px;width:205px">Contact Information</h4>
  <div class="abs contact-row" style="top:74px"><svg width="12" height="16" viewBox="0 0 12 16"><path d="M6 15 C2 10 1 8 1 6 A5 5 0 0 1 11 6 C11 8 10 10 6 15 Z" fill="none" stroke="var(--teal)" stroke-width="1.8"/><circle cx="6" cy="6" r="1.8" fill="var(--teal)"/></svg><div>DORNABY<br><span style="display:inline-block;margin-top:4px">123 euismod cidun ut laoreet<br>laoreet dol magna aliquam</span></div></div>
  <div class="abs contact-row plain" style="top:150px"><svg width="12" height="16" viewBox="0 0 12 16"><path d="M3 1 C0 3 0 10 5 14 C7 15 9 15 10 14 L11 11 L8 9 L6 11 C4 9 3 7 3 5 L5 4 L5 1 Z" fill="var(--teal)"/></svg><div>(012) 555 0147</div></div>
  <div class="abs contact-row plain" style="top:188px"><svg width="13" height="16" viewBox="0 0 13 16"><path d="M0 4 H13 L6.5 8 Z M0 6 L6.5 10 L13 6 V13 H0 Z" fill="var(--teal)"/></svg><div>info@dornaby.com</div></div>
  <div class="abs footer-sep" style="left:539px"></div>

  <h4 class="abs footer-heading" style="left:580px;width:250px">Location Map</h4>
  <div class="abs map-area" role="img" aria-label="Street map showing the office location"></div>
  <div class="abs footer-sep" style="left:875px"></div>

  <div class="abs footer-brand">
    <div class="name">Dornaby</div>
    <div class="tag">Accounting and Bookkeeping</div>
  </div>
  <div class="abs social" aria-label="Social links"><span class="s1"></span><span class="s2"></span><span class="s3"></span><span class="s4"></span></div>
</footer>

<div class="copyright">Copyright &copy; 2016 Dornaby Accounting and Bookkeeping. &nbsp;All Rights Reserved.</div>

</body>
</html>
```